Brookvane Consulting Business Card Design

Business Card Design for Brookvane Consulting. Brookvane Consulting is a boutique consultancy based in Atlanta, GA., that specializes in marketing strategy, organization planning, and leadership development. We provide solutions for small businesses and startups as well as Vantage 300 companies.

http://brookvaneconsulting.com/

Target Market(s)

We provide solutions for small businesses and startups as well as Vantage 300 companies.

Industry/Entity Type

Consulting

Contact Information for Business Card

Two sided business card with priority on contact information, logo, tag line (Guidance to Plan Better, Lead Better, Grow Further)

Colors

Designer to choose colors to be used in the design.

Requirements
Must have
• contact information, logo, tag line (Guidance to Plan Better, Lead Better, Grow Further)
• Simple no over communication.
Nice to have
• I would like to see different placements of logo and creative use of both sides of the card
Should not have
• Do not put too much information on the card.

```html
<!DOCTYPE html>
<html lang="en">
<head>
<meta charset="utf-8">
<title>Brookvane Consulting Business Card</title>
<link href="https://fonts.googleapis.com/css2?family=Lato:wght@400;700&display=swap" rel="stylesheet">
<style>
  :root {
    --backdrop: #3a322d;
    --card-dark: #151517;
    --card-mid: #1f1f22;
    --ink-white: #ffffff;
    --ink-grey: #b9b9bd;
    --ink-soft: #8d8d92;
  }
  * { margin: 0; padding: 0; box-sizing: border-box; }
  html, body { width: 1200px; height: 769px; overflow: hidden; }
  body {
    background: var(--backdrop);
    font-family: "Lato", sans-serif;
    position: relative;
  }
  .card {
    position: absolute;
    top: 230px;
    width: 540px;
    height: 309px;
    border-radius: 4px;
    overflow: hidden;
    box-shadow: 0 14px 34px rgba(0,0,0,0.45);
  }
  .card--contact { left: 40px; }
  .card--brand { left: 620px; }
  .card-texture {
    position: absolute;
    inset: 0;
    background: linear-gradient(135deg, var(--card-mid) 0%, var(--card-dark) 60%, #101012 100%);
  }
  .brand-name {
    position: relative;
    color: var(--ink-white);
    font-weight: 700;
    letter-spacing: 0.5px;
    display: flex;
    align-items: center;
    gap: 10px;
    white-space: nowrap;
  }
  .brand-mark {
    width: 12px;
    height: 12px;
    background: var(--ink-white);
    flex: none;
  }
  .card--contact .brand-name {
    position: absolute;
    left: 40px;
    top: 52px;
    font-size: 30px;
  }
  .person {
    position: absolute;
    left: 40px;
    top: 150px;
  }
  .person-name {
    color: var(--ink-soft);
    font-weight: 700;
    font-size: 17px;
    letter-spacing: 0.6px;
    text-transform: uppercase;
  }
  .person-role {
    color: var(--ink-white);
    font-size: 14px;
    margin-top: 2px;
  }
  .contact-list {
    list-style: none;
    margin-top: 14px;
  }
  .contact-list li {
    display: flex;
    align-items: center;
    gap: 10px;
    color: var(--ink-white);
    font-size: 13.5px;
    line-height: 22px;
  }
  .contact-list svg { width: 13px; height: 13px; flex: none; }
  .card--brand .brand-block {
    position: absolute;
    left: 0; right: 0;
    top: 100px;
    display: flex;
    flex-direction: column;
    align-items: center;
  }
  .card--brand .brand-name { font-size: 36px; }
  .tagline {
    margin-top: 38px;
    color: var(--ink-grey);
    font-size: 12.5px;
    letter-spacing: 0.3px;
    white-space: nowrap;
  }
</style>
</head>
<body>

  <section class="card card--contact">
    <div class="card-texture" role="img" aria-label="Dark card surface with a subtle tonal pattern of small triangles"></div>
    <div class="brand-name"><span class="brand-mark"></span>Brookvane Consulting</div>
    <div class="person">
      <div class="person-name">Dario Whitfield</div>
      <div class="person-role">Founder/Managing Director</div>
      <ul class="contact-list">
        <li>
          <svg viewBox="0 0 16 16" aria-hidden="true"><path fill="#b9b9bd" d="M3.6 1.5l2.2 2.6-1.3 1.7c.9 2 2.5 3.6 4.5 4.5l1.7-1.3 2.6 2.2-1.2 2.3C7 13.6 2.4 9 1.5 3.6z"/></svg>
          424-555-0148
        </li>
        <li>
          <svg viewBox="0 0 16 16" aria-hidden="true"><rect x="1" y="3" width="14" height="10" fill="#b9b9bd"/><path d="M1 3l7 6 7-6" fill="none" stroke="#151517" stroke-width="1.4"/></svg>
          dario@brookvaneconsulting.com
        </li>
        <li>
          <svg viewBox="0 0 16 16" aria-hidden="true"><circle cx="8" cy="8" r="6.5" fill="none" stroke="#b9b9bd" stroke-width="1.5"/><path d="M1.5 8h13M8 1.5c-3 3.5-3 9.5 0 13M8 1.5c3 3.5 3 9.5 0 13" fill="none" stroke="#b9b9bd" stroke-width="1.1"/></svg>
          brookvaneconsulting.com
        </li>
      </ul>
    </div>
  </section>

  <section class="card card--brand">
    <div class="card-texture" role="img" aria-label="Dark card surface with a subtle tonal pattern of small triangles"></div>
    <div class="brand-block">
      <div class="brand-name"><span class="brand-mark"></span>Brookvane Consulting</div>
      <p class="tagline">Guidance to Plan Better, Lead Better, Grow Further</p>
    </div>
  </section>

</body>
</html>
```